brightquokka.net we need a webpage designed for our new product

We need a webpage designed for our new range of products from our new brand. We have had a logo designed on sketchharbor (see attached) and we want to keep to this theme. Our first product is a range of affordable app controlled LED lightbulbs.

I have added some photos that we think is good inspirational material and would be good as a background to this website, but we want the site to look modern but not conventional. We would like something that makes our company look quirky not corporate.

Thats it

Target Market(s)

Our product is being stocked by big name online retailers in the UK, the page will get link through hits from our app. Our target market is gadget freaks of all ages.

Industry/Entity Type

It Company

Requirements
Must have
• We are going to need a help page, text to be uploaded next few days.

We need a contact page.

design my work on iOS and Android as most people will access page through their handset or tablet.
Should not have
• We do not want anything too corporate.

```html
<!DOCTYPE html>
<html lang="en">
<head>
<meta charset="utf-8">
<title>Brightquokka – Home</title>
<link href="https://fonts.googleapis.com/css2?family=Open+Sans:wght@400;600&family=PT+Sans&display=swap" rel="stylesheet">
<style>
:root{
  --green:#4aab48;
  --green-dark:#3f9a3d;
  --link-green:#4a9e47;
  --ink:#1c1c1c;
  --white:#ffffff;
  --panel-shadow:rgba(0,0,0,.25);
}
*{margin:0;padding:0;box-sizing:border-box}
html,body{width:1148px;height:1200px;overflow:hidden;background:var(--white)}
body{position:relative;font-family:"Open Sans",sans-serif;color:var(--ink)}
.abs{position:absolute}
.top-rule{left:0;top:0;width:1148px;height:5px;background:var(--green)}
.main-nav{left:0;top:122px;width:1148px;height:52px;background:var(--green)}
.main-nav a{position:absolute;top:0;line-height:52px;font-family:"PT Sans",sans-serif;font-size:14.5px;color:var(--white);text-decoration:none;letter-spacing:.2px}
.brand-panel{left:479px;top:0;width:191px;height:272px;background:var(--white);box-shadow:0 2px 8px var(--panel-shadow);z-index:3;display:flex;flex-direction:column;align-items:center;justify-content:flex-end;padding-bottom:22px}
.brand-mark{width:18px;height:18px;background:var(--green);margin-bottom:10px}
.brand-name{font-family:"Open Sans",sans-serif;font-weight:600;font-size:13px;color:var(--green);letter-spacing:1px}
.social{top:61px;display:flex;align-items:center;gap:6px;font-size:11px;font-weight:600;color:var(--green)}
.social span.box{width:10px;height:10px;background:var(--green)}
.hero{left:0;top:174px;width:1148px;height:428px;background:linear-gradient(100deg,#6e6150 0%,#a39583 22%,#c9bfae 45%,#8a7a67 65%,#b8a891 85%,#7d6a55 100%)}
.hero-arrow{top:412px;width:40px;height:40px;border-radius:50%;background:rgba(40,40,40,.55)}
.hero-arrow svg{display:block}
h2{position:absolute;font-weight:400;font-size:26px;color:var(--ink)}
.welcome p{position:absolute;left:112px;width:622px;font-size:12px;line-height:23px}
.btn{left:112px;top:836px;width:86px;height:30px;border-radius:6px;background:var(--green);color:var(--white);font-size:12.5px;line-height:30px;text-align:center}
.blog-thumb{left:758px;width:48px;border-radius:4px}
.blog-text{left:814px;width:224px;font-size:12.5px;line-height:17.5px}
.more{font-size:12.5px;color:var(--link-green)}
.product-photo{top:938px;width:222px;height:118px;border-radius:3px}
.product-text{top:1065px;width:214px;font-size:12.5px;line-height:18px;text-align:justify;text-align-last:left}
.footer{left:0;top:1148px;width:1148px;height:52px;background:var(--green)}
.footer-links{left:106px;top:0;line-height:52px;font-size:13.5px;color:var(--white)}
.footer-links .sep{margin:0 8px;font-size:10px}
.copyright{left:874px;top:0;line-height:54px;font-size:11px;color:var(--white)}
</style>
</head>
<body>
<div class="abs top-rule"></div>

<div class="abs brand-panel">
  <div class="brand-mark"></div>
  <div class="brand-name">BRIGHTQUOKKA</div>
</div>

<div class="abs social" style="left:904px"><span class="box"></span>Friendloop</div>
<div class="abs social" style="left:904px;top:79px"><span class="box"></span>Chirpline</div>
<div class="abs social" style="left:984px"><span class="box"></span>Vidstream</div>

<nav class="abs main-nav">
  <a href="#" style="left:210px">HOME</a>
  <a href="#" style="left:276px">ABOUT US</a>
  <a href="#" style="left:366px">SERVICES</a>
  <a href="#" style="left:716px">BLOG</a>
  <a href="#" style="left:778px">PRODUCTS</a>
  <a href="#" style="left:873px">CONTACT US</a>
</nav>

<div class="abs hero" role="img" aria-label="Photo of a large vintage warehouse filled with lamps, arcade machines, toys and figures"></div>
<div class="abs hero-arrow" style="left:14px"><svg width="40" height="40"><polygon points="23,13 15,20 23,27" fill="#fff"/></svg></div>
<div class="abs hero-arrow" style="left:1086px"><svg width="40" height="40"><polygon points="17,13 25,20 17,27" fill="#fff"/></svg></div>

<section class="welcome">
  <h2 style="left:112px;top:626px">Welcome Text</h2>
  <p style="top:666px">Neque porro quisquam est, qui dolorem ipsum quia dolor sit amet, consectetur, adipisci velit, sed quia non numquam eius modi tempora incidunt ut labore et dolore magnam aliquam quaerat voluptatem. Ut enim ad minima veniam, quis nostrum exercitationem ullam corporis suscipit laboriosam</p>
  <p style="top:758px">Neque porro quisquam est, qui dolorem ipsum quia dolor sit amet, consectetur, adipisci velit, sed quia non numquam eius modi tempora incidunt ut labore et dolore magnam aliquam quaerat voluptatem. Ut enim ad minima veniam, quis nostrum exercitationem ullam corporis suscipit laboriosam</p>
  <div class="abs btn">Read more</div>
</section>

<section class="blog">
  <h2 style="left:757px;top:632px">Blog</h2>
  <div class="abs blog-thumb" role="img" aria-label="Blog photo of golden figurines" style="top:683px;height:52px;background:linear-gradient(135deg,#6b4a2a,#d9a040,#5a3a20)"></div>
  <div class="abs blog-text" style="top:682px">Duis aute irure dolor in reprehenderit in voluptate velit esse cillum dolore eu fugiat nulla pariatur.</div>
  <div class="abs more" style="left:971px;top:732px">Read more</div>
  <div class="abs blog-thumb" role="img" aria-label="Blog photo of a vintage figure" style="top:758px;height:52px;background:linear-gradient(135deg,#8a6a4a,#e8dccb,#6a4a30)"></div>
  <div class="abs blog-text" style="top:757px">Duis aute irure dolor in reprehenderit in voluptate velit esse cillum dolore eu fugiat nulla pariatur.</div>
  <div class="abs more" style="left:971px;top:801px">Read more</div>
</section>

<section class="products">
  <h2 style="left:116px;top:890px">Products</h2>
  <div class="abs product-photo" role="img" aria-label="Photo of LED spotlight bulbs" style="left:118px;background:linear-gradient(135deg,#f2f2f2,#b9b9b9,#eeeeee)"></div>
  <div class="abs product-photo" role="img" aria-label="Photo of white LED bulbs on wood" style="left:349px;background:linear-gradient(135deg,#5a3a22,#e9e7e2,#7a5236)"></div>
  <div class="abs product-photo" role="img" aria-label="Photo of glowing blue LED bulbs" style="left:579px;background:linear-gradient(135deg,#1b4fa0,#8fc0f0,#0c2a6a)"></div>
  <div class="abs product-photo" role="img" aria-label="Photo of a glowing filament bulb on dark background" style="left:810px;background:radial-gradient(circle at 60% 40%,#f2c24a 0%,#7a3f8a 25%,#18203a 60%)"></div>

  <div class="abs product-text" style="left:117px">Duis aute reprehenderit in voluptate velit esse.</div>
  <div class="abs product-text" style="left:353px">Duis aute reprehenderit in voluptate velit esse.</div>
  <div class="abs product-text" style="left:586px;top:1067px">Duis aute reprehenderit in voluptate velit esse.</div>
  <div class="abs product-text" style="left:817px;top:1067px">Duis aute reprehenderit in voluptate velit esse.</div>

  <div class="abs more" style="left:118px;top:1109px">Read more</div>
  <div class="abs more" style="left:352px;top:1109px">Read more</div>
  <div class="abs more" style="left:584px;top:1109px">Read more</div>
  <div class="abs more" style="left:818px;top:1109px">Read more</div>
</section>

<footer class="abs footer">
  <div class="abs footer-links">Home<span class="sep">::</span>About Us<span class="sep">::</span>Services<span class="sep">::</span>Products<span class="sep">::</span>Blog<span class="sep">::</span>Contact Us</div>
  <div class="abs copyright">© 2014.www.lumenfoldco.com</div>
</footer>
</body>
</html>
```